Military and tactical gear supply company needs web design

We need a web design for a company called U.S. Torvane. We provide quality tactical equipment to military and law enforcement. This is an e-commerce business and we primarily market ourselves on social media. Our key products are backpacks, military-style belts, and tactical flashlights. The gear we sell is not yet widely known about, but is on par with the state-of-the-art products in this field. We want the website to convey the message of quality, durability, and reliability. We use the word "kinetic" because the customers in this field are very "action-oriented" and we would like that idea to be communicated in the web site as well. The primary demographic is men in their 20's-30's, so the web site should have a masculine feel to it. Attached is the logo and color scheme.

```html
<!DOCTYPE html>
<html lang="en">
<head>
<meta charset="utf-8">
<title>U.S. Torvane — Tactical Gear</title>
<link href="https://fonts.googleapis.com/css2?family=Oswald:wght@500;600;700&family=Lato:wght@400;700;900&display=swap" rel="stylesheet">
<style>
:root{
  --red:#c61f2e;
  --red-dark:#a3172a;
  --ink:#1b1c1f;
  --ink-2:#26282c;
  --slate:#3f5f7c;
  --slate-2:#52718d;
  --paper:#ffffff;
  --mist:#f1f2f4;
  --line:#e1e3e7;
  --text:#2c2e33;
  --muted:#6c7079;
  --gold:#f2a20c;
}
*{box-sizing:border-box;margin:0;padding:0}
html,body{width:1200px;height:4828px;overflow:hidden}
body{font-family:"Lato",Arial,sans-serif;color:var(--text);background:var(--paper);position:relative}
.heading{font-family:"Oswald","Arial Narrow",sans-serif;text-transform:uppercase;letter-spacing:.5px}
.accent{color:var(--red)}
a{color:inherit;text-decoration:none}

/* top bar */
.topbar{height:36px;background:#111214;color:#c9ccd2;font-size:13px;display:flex;align-items:center;justify-content:space-between;padding:0 112px}
.topbar span+span{margin-left:22px}
/* header */
.header{height:80px;background:var(--ink);display:flex;align-items:center;padding:0 112px}
.brand{display:flex;align-items:center;gap:10px;color:#fff;font-family:"Oswald",sans-serif;font-weight:700;font-size:30px;letter-spacing:1px;width:260px}
.brand i{width:18px;height:18px;background:var(--red);display:block}
.search{margin-left:70px;width:470px;height:38px;background:#fff;border-radius:3px;display:flex;align-items:center;padding:0 14px;color:#9aa0a8;font-size:13px;gap:10px}
.cart{margin-left:auto;color:#fff;font-size:13px;display:flex;align-items:center;gap:10px;font-weight:700}
.cart b{background:var(--red);width:20px;height:20px;border-radius:50%;display:grid;place-items:center;font-size:11px}
/* nav */
.nav{height:34px;background:var(--red);display:flex;padding:0 112px}
.nav a{flex:1;display:flex;align-items:center;justify-content:center;color:#fff;font-size:13px;font-weight:700;letter-spacing:1px}
.nav a.active{background:#fff;color:var(--red);border-bottom:3px solid var(--ink)}
.perks{height:30px;background:#fff;border-bottom:1px solid var(--line);display:flex;justify-content:center;gap:70px;align-items:center;font-size:12px;color:var(--muted);font-weight:700}
.perks span{display:flex;align-items:center;gap:8px}
/* hero */
.hero{position:relative;height:630px;background:linear-gradient(100deg,#3b3328 0%,#6d5a3e 40%,#9a6b3a 65%,#5b4a35 100%)}
.hero-shade{position:absolute;inset:0;background:linear-gradient(90deg,rgba(15,14,12,.75) 0%,rgba(15,14,12,.2) 55%,rgba(15,14,12,0) 100%)}
.hero-copy{position:absolute;left:112px;top:290px;color:#fff}
.hero-copy h1{font-size:64px;line-height:1.05;font-weight:700}
.hero-copy p{margin-top:14px;font-size:14px;font-weight:700;letter-spacing:.5px}
.btn{display:inline-flex;align-items:center;justify-content:center;height:44px;padding:0 28px;font-size:13px;font-weight:900;letter-spacing:1px;text-transform:uppercase}
.btn-red{background:var(--red);color:#fff}
.hero-copy .btn{margin-top:22px}
.hero-edge{position:absolute;left:0;bottom:-1px;width:1200px;height:50px}
/* welcome */
.welcome{position:relative;height:660px;background:var(--mist)}
.welcome-photo{position:absolute;left:150px;top:80px;width:330px;height:470px;background:linear-gradient(160deg,#7c7866,#4d4a3e 60%,#2e2c25)}
.welcome-frame{position:absolute;left:138px;top:64px;width:80px;height:500px;border:10px solid var(--red);border-right:none}
.welcome-copy{position:absolute;left:590px;top:130px;width:480px}
.welcome-copy h2{font-size:48px;font-weight:700;color:var(--ink)}
.welcome-copy p{margin-top:16px;font-size:14px;line-height:1.7;color:var(--muted)}
.btn-outline{margin-top:34px;border:2px solid var(--ink);color:var(--ink);box-shadow:6px 6px 0 var(--red)}
/* products */
.products{position:relative;height:1680px;padding:0 112px}
.flag{position:absolute;right:0;top:600px;width:280px;height:700px;background:linear-gradient(180deg,rgba(63,95,124,.15),rgba(198,31,46,.18));clip-path:polygon(40% 0,100% 0,100% 100%,0 100%)}
.section-title{font-size:30px;font-weight:700;color:var(--ink);padding-top:70px}
.section-title::after{content:"";display:block;width:70px;height:4px;background:var(--red);margin-top:8px}
.card{position:relative;width:976px;height:428px;background:#fff;border:1px solid var(--line);box-shadow:0 6px 22px rgba(0,0,0,.07);margin-top:28px;padding:46px 40px}
.card h3{font-size:40px;font-weight:700;color:var(--ink)}
.card p{margin-top:16px;width:470px;font-size:14px;line-height:1.7;color:var(--muted)}
.card p+p{margin-top:10px}
.price{position:absolute;left:40px;bottom:46px}
.price strong{font-size:34px;font-family:"Oswald",sans-serif;color:var(--ink)}
.price strong sup{font-size:18px}
.stars{display:flex;align-items:center;gap:3px;margin-top:2px;font-size:12px;color:var(--muted)}
.stars svg{width:15px;height:15px}
.stars em{font-style:normal;margin-left:6px}
.shop{position:absolute;left:330px;bottom:58px;display:flex;height:44px}
.shop i{width:36px;background:var(--slate);display:grid;place-items:center}
.shop span{background:var(--red);color:#fff;font-weight:900;font-size:13px;letter-spacing:1px;padding:0 26px;display:flex;align-items:center;clip-path:polygon(0 0,100% 0,90% 100%,0 100%)}
.product-photo{position:absolute;right:50px;top:60px;width:290px;height:300px}
.explore{display:flex;justify-content:center;margin-top:48px}
.explore .btn{border:2px solid var(--ink);color:var(--ink);box-shadow:6px 6px 0 var(--slate)}
/* testimonial */
.testimonial{position:relative;height:368px;background:linear-gradient(90deg,#2d2f27,#4b4a3c 50%,#2a2c25);color:#fff;text-align:center}
.testimonial::before{content:"";position:absolute;inset:0;background:rgba(15,16,18,.6)}
.testimonial .inner{position:relative;padding-top:40px}
.testimonial h2{font-size:34px;font-weight:700}
.testimonial .rate{display:flex;justify-content:center;gap:3px;margin-top:10px}
.testimonial blockquote{margin:14px auto 0;width:900px;font-size:16px;font-style:italic;font-weight:700;line-height:1.6}
.author{display:flex;justify-content:center;align-items:center;gap:14px;margin-top:22px;text-align:left}
.author i{width:48px;height:48px;border-radius:50%;background:#8c8a7a;display:block}
.author b{display:block;font-size:15px}
.author small{font-size:12px;color:#c9ccd2}
/* blogs */
.blogs{height:680px;padding:0 112px}
.blogs .section-title{text-align:center;font-size:40px;padding-top:70px}
.blogs .section-title::after{margin:8px auto 0}
.blog-grid{display:flex;gap:24px;margin-top:34px}
.post{width:309px}
.post-photo{position:relative;height:222px}
.post-date{position:absolute;left:12px;top:12px;width:44px;height:48px;background:#fff;color:var(--ink);font-size:11px;font-weight:900;text-align:center;padding-top:6px;line-height:1.2}
.post h4{margin-top:16px;font-size:19px;font-weight:900;color:var(--ink)}
.post p{margin-top:8px;font-size:13px;line-height:1.6;color:var(--muted)}
.post a{display:inline-block;margin-top:10px;font-size:12px;font-weight:900;color:var(--red);letter-spacing:1px}
/* split cta */
.cta{display:flex;height:380px}
.cta > div{flex:1;padding:70px 0 0 112px;color:#fff;position:relative}
.cta .news{background:var(--red)}
.cta .about{background:var(--slate);padding-left:90px}
.cta h2{font-size:34px;font-weight:700;line-height:1.1}
.cta p{margin-top:14px;width:420px;font-size:14px;line-height:1.6;font-weight:700}
.subscribe{display:flex;margin-top:28px;height:48px;width:400px}
.subscribe span{flex:1;background:#fff;color:#9aa0a8;font-size:13px;display:flex;align-items:center;padding-left:18px}
.subscribe b{background:var(--ink);color:#fff;font-size:13px;letter-spacing:1px;padding:0 26px;display:flex;align-items:center}
.btn-white{margin-top:28px;background:#fff;color:var(--red);box-shadow:6px 6px 0 var(--ink)}
/* footer */
.footer{height:264px;background:var(--ink-2);color:#d4d7dc;display:flex;padding:50px 112px 0}
.footer .brand{width:auto;font-size:34px}
.social{display:flex;gap:10px;margin-top:22px}
.social i{width:32px;height:32px;border:1px solid #8b9099;border-radius:50%;display:block}
.links{margin-left:110px;display:flex;gap:80px;font-size:13px;line-height:2}
.help{margin-left:auto;font-size:13px}
.help .phone{display:flex;align-items:center;gap:10px;font-size:18px;font-weight:900;color:#fff;margin:10px 0}
.help .btn{margin-top:16px;height:40px}
.copyright{height:48px;background:#121315;color:#9aa0a8;font-size:12px;display:flex;align-items:center;justify-content:center}
</style>
</head>
<body>

<div class="topbar">
  <div><span>Contact Our Team: +1 800-555-0142</span></div>
  <div><span>Change Currency: USD</span><span>Login</span><span>Register</span></div>
</div>

<header class="header">
  <div class="brand"><i></i>U.S. TORVANE</div>
  <div class="search">
    <svg width="14" height="14" viewBox="0 0 16 16" fill="none" stroke="#9aa0a8" stroke-width="2"><circle cx="7" cy="7" r="5"/><path d="M11 11l4 4"/></svg>
    Search
  </div>
  <div class="cart">
    <svg width="22" height="20" viewBox="0 0 24 22" fill="none" stroke="#fff" stroke-width="2"><path d="M1 2h4l3 12h12l3-9H6"/><circle cx="9" cy="19" r="1.6"/><circle cx="19" cy="19" r="1.6"/></svg>
    CART <b>0</b>
  </div>
</header>

<nav class="nav">
  <a class="active" href="#">HOME</a><a href="#">ABOUT</a><a href="#">PRODUCTS</a><a href="#">CUSTOMER SERVICE</a><a href="#">BLOG</a>
</nav>

<div class="perks">
  <span><svg width="16" height="12" viewBox="0 0 18 12" fill="var(--red)"><rect width="11" height="9"/><path d="M11 3h4l3 3v3h-7z"/></svg>FREE U.S. SHIPPING</span>
  <span><svg width="14" height="14" viewBox="0 0 14 14" fill="var(--red)"><path d="M7 0l6 3v4c0 4-3 6-6 7-3-1-6-3-6-7V3z"/></svg>1 YEAR WARRANTY</span>
  <span><svg width="14" height="14" viewBox="0 0 14 14" fill="var(--red)"><circle cx="7" cy="7" r="7"/></svg>ELITE CUSTOMER SERVICE</span>
</div>

<section class="hero" role="img" aria-label="Soldier in full combat gear advancing through smoke and fire">
  <div class="hero-shade"></div>
  <div class="hero-copy">
    <h1 class="heading">Quality,<br>Durability,<br>and Reliability</h1>
    <p>DESIGNED FOR PROFESSIONALS - AVAILABLE FOR CIVILIANS</p>
    <a class="btn btn-red" href="#">Browse Our Products</a>
  </div>
  <svg class="hero-edge" viewBox="0 0 1200 50" preserveAspectRatio="none"><polygon points="0,50 1200,0 1200,50" fill="#f1f2f4"/></svg>
</section>

<section class="welcome">
  <div class="welcome-frame"></div>
  <div class="welcome-photo" role="img" aria-label="Soldier in helmet and headset shouting a command"></div>
  <div class="welcome-copy">
    <h2 class="heading">Welcome to <span class="accent">U.S. Torvane</span></h2>
    <p>Lorem ipsum dolor sit amet, consectetur adipiscing elit, do eiusmod tempor incididunt ut labore et dolor ue. Quis ipsum suspendisse ultrices gravida. Risus commodo viverra maecenas accumsan.</p>
    <p>Lorem ipsum dolor sit amet, consectetur adipiscing elit, do eiusmod tempor incididunt ut labore et dolore magna aliqua. Quis ipsum suspendisse ultrices gravida.</p>
    <a class="btn btn-outline" href="#">Learn More</a>
  </div>
</section>

<section class="products">
  <div class="flag" aria-hidden="true"></div>
  <h2 class="section-title heading">Explore Our <span class="accent">Product</span></h2>

  <article class="card">
    <h3 class="heading">Military-Style Belts</h3>
    <p>Lorem ipsum dolor sit amet, consectetur adipiscing elit, do eiusmod tempor incididunt ut labore et dolore magna aliqua. Quis ipsum suspendisse ultrices gravida. Risus commodo viverra accumsan lacus vel facilisis.</p>
    <p>Lorem ipsum dolor sit amet, consectetur adipiscing elit, do eiusmod tempor incididunt ut labore et dolore magna aliqua. Quis ipsum suspendisse ultrices gravida.</p>
    <div class="price"><strong><sup>$</sup>219.98</strong>
      <div class="stars"><svg viewBox="0 0 10 10"><path fill="var(--gold)" d="M5 0l1.5 3.3 3.5.3-2.7 2.3.9 3.6L5 7.6 1.8 9.5l.9-3.6L0 3.6l3.5-.3z"/></svg><svg viewBox="0 0 10 10"><path fill="var(--gold)" d="M5 0l1.5 3.3 3.5.3-2.7 2.3.9 3.6L5 7.6 1.8 9.5l.9-3.6L0 3.6l3.5-.3z"/></svg><svg viewBox="0 0 10 10"><path fill="var(--gold)" d="M5 0l1.5 3.3 3.5.3-2.7 2.3.9 3.6L5 7.6 1.8 9.5l.9-3.6L0 3.6l3.5-.3z"/></svg><svg viewBox="0 0 10 10"><path fill="var(--gold)" d="M5 0l1.5 3.3 3.5.3-2.7 2.3.9 3.6L5 7.6 1.8 9.5l.9-3.6L0 3.6l3.5-.3z"/></svg><svg viewBox="0 0 10 10"><path fill="var(--gold)" d="M5 0l1.5 3.3 3.5.3-2.7 2.3.9 3.6L5 7.6 1.8 9.5l.9-3.6L0 3.6l3.5-.3z"/></svg><em>(120 Reviews)</em></div>
    </div>
    <a class="shop" href="#"><i><svg width="18" height="16" viewBox="0 0 24 22" fill="none" stroke="#fff" stroke-width="2"><path d="M1 2h4l3 12h12l3-9H6"/></svg></i><span>SHOP NOW</span></a>
    <div class="product-photo" role="img" aria-label="Olive tactical belt coiled with metal buckle" style="background:radial-gradient(circle at 50% 50%,#8d8a6c 0%,#6f6c52 45%,#fff 72%)"></div>
  </article>

  <article class="card">
    <h3 class="heading">Military-Backpacks</h3>
    <p>Lorem ipsum dolor sit amet, consectetur adipiscing elit, do eiusmod tempor incididunt ut labore et dolore magna aliqua. Quis ipsum suspendisse ultrices gravida. Risus commodo viverra accumsan lacus vel facilisis.</p>
    <p>Lorem ipsum dolor sit amet, consectetur adipiscing elit, do eiusmod tempor incididunt ut labore et dolore magna aliqua. Quis ipsum suspendisse ultrices gravida.</p>
    <div class="price"><strong><sup>$</sup>219.98</strong>
      <div class="stars"><svg viewBox="0 0 10 10"><path fill="var(--gold)" d="M5 0l1.5 3.3 3.5.3-2.7 2.3.9 3.6L5 7.6 1.8 9.5l.9-3.6L0 3.6l3.5-.3z"/></svg><svg viewBox="0 0 10 10"><path fill="var(--gold)" d="M5 0l1.5 3.3 3.5.3-2.7 2.3.9 3.6L5 7.6 1.8 9.5l.9-3.6L0 3.6l3.5-.3z"/></svg><svg viewBox="0 0 10 10"><path fill="var(--gold)" d="M5 0l1.5 3.3 3.5.3-2.7 2.3.9 3.6L5 7.6 1.8 9.5l.9-3.6L0 3.6l3.5-.3z"/></svg><svg viewBox="0 0 10 10"><path fill="var(--gold)" d="M5 0l1.5 3.3 3.5.3-2.7 2.3.9 3.6L5 7.6 1.8 9.5l.9-3.6L0 3.6l3.5-.3z"/></svg><svg viewBox="0 0 10 10"><path fill="var(--gold)" d="M5 0l1.5 3.3 3.5.3-2.7 2.3.9 3.6L5 7.6 1.8 9.5l.9-3.6L0 3.6l3.5-.3z"/></svg><em>(120 Reviews)</em></div>
    </div>
    <a class="shop" href="#"><i><svg width="18" height="16" viewBox="0 0 24 22" fill="none" stroke="#fff" stroke-width="2"><path d="M1 2h4l3 12h12l3-9H6"/></svg></i><span>SHOP NOW</span></a>
    <div class="product-photo" role="img" aria-label="Tan military backpack with straps and pouches" style="background:radial-gradient(ellipse 40% 50% at 50% 50%,#b8b08c 0%,#9d9574 60%,#fff 100%)"></div>
  </article>

  <article class="card">
    <h3 class="heading">Tactical Flashlights</h3>
    <p>Lorem ipsum dolor sit amet, consectetur adipiscing elit, do eiusmod tempor incididunt ut labore et dolore magna aliqua. Quis ipsum suspendisse ultrices gravida. Risus commodo viverra accumsan lacus vel facilisis.</p>
    <p>Lorem ipsum dolor sit amet, consectetur adipiscing elit, do eiusmod tempor incididunt ut labore et dolore magna aliqua. Quis ipsum suspendisse ultrices gravida.</p>
    <div class="price"><strong><sup>$</sup>219.98</strong>
      <div class="stars"><svg viewBox="0 0 10 10"><path fill="var(--gold)" d="M5 0l1.5 3.3 3.5.3-2.7 2.3.9 3.6L5 7.6 1.8 9.5l.9-3.6L0 3.6l3.5-.3z"/></svg><svg viewBox="0 0 10 10"><path fill="var(--gold)" d="M5 0l1.5 3.3 3.5.3-2.7 2.3.9 3.6L5 7.6 1.8 9.5l.9-3.6L0 3.6l3.5-.3z"/></svg><svg viewBox="0 0 10 10"><path fill="var(--gold)" d="M5 0l1.5 3.3 3.5.3-2.7 2.3.9 3.6L5 7.6 1.8 9.5l.9-3.6L0 3.6l3.5-.3z"/></svg><svg viewBox="0 0 10 10"><path fill="var(--gold)" d="M5 0l1.5 3.3 3.5.3-2.7 2.3.9 3.6L5 7.6 1.8 9.5l.9-3.6L0 3.6l3.5-.3z"/></svg><svg viewBox="0 0 10 10"><path fill="var(--gold)" d="M5 0l1.5 3.3 3.5.3-2.7 2.3.9 3.6L5 7.6 1.8 9.5l.9-3.6L0 3.6l3.5-.3z"/></svg><em>(120 Reviews)</em></div>
    </div>
    <a class="shop" href="#"><i><svg width="18" height="16" viewBox="0 0 24 22" fill="none" stroke="#fff" stroke-width="2"><path d="M1 2h4l3 12h12l3-9H6"/></svg></i><span>SHOP NOW</span></a>
    <div class="product-photo" role="img" aria-label="Black tactical flashlight lying diagonally" style="background:linear-gradient(135deg,#fff 30%,#2a2b2e 45%,#151618 55%,#fff 70%)"></div>
  </article>

  <div class="explore"><a class="btn" href="#">Explore All Products</a></div>
</section>

<section class="testimonial" role="img" aria-label="Soldiers on patrol in a blurred field setting">
  <div class="inner">
    <h2 class="heading">What Our Client Says</h2>
    <div class="rate">
      <svg width="14" height="14" viewBox="0 0 10 10"><path fill="var(--gold)" d="M5 0l1.5 3.3 3.5.3-2.7 2.3.9 3.6L5 7.6 1.8 9.5l.9-3.6L0 3.6l3.5-.3z"/></svg><svg width="14" height="14" viewBox="0 0 10 10"><path fill="var(--gold)" d="M5 0l1.5 3.3 3.5.3-2.7 2.3.9 3.6L5 7.6 1.8 9.5l.9-3.6L0 3.6l3.5-.3z"/></svg><svg width="14" height="14" viewBox="0 0 10 10"><path fill="var(--gold)" d="M5 0l1.5 3.3 3.5.3-2.7 2.3.9 3.6L5 7.6 1.8 9.5l.9-3.6L0 3.6l3.5-.3z"/></svg><svg width="14" height="14" viewBox="0 0 10 10"><path fill="var(--gold)" d="M5 0l1.5 3.3 3.5.3-2.7 2.3.9 3.6L5 7.6 1.8 9.5l.9-3.6L0 3.6l3.5-.3z"/></svg><svg width="14" height="14" viewBox="0 0 10 10"><path fill="var(--gold)" d="M5 0l1.5 3.3 3.5.3-2.7 2.3.9 3.6L5 7.6 1.8 9.5l.9-3.6L0 3.6l3.5-.3z"/></svg>
    </div>
    <blockquote>“Lorem ipsum dolor sit amet, consectetur adipiscing elit, sed do eiusmod tempor incididunt ut labore et dolore magna aliqua. Quis ipsum suspendisse ultrices gravida. Risus commodo viverra maecenas accumsan lacus vel facilisis. Lorem ipsum dolor sit amet, consectetur adipiscing elit.”</blockquote>
    <div class="author"><i role="img" aria-label="Client portrait"></i><div><b>Mark Hale</b><small>Lorem ipsum dolor</small></div></div>
  </div>
</section>

<section class="blogs">
  <h2 class="section-title heading">Latest <span class="accent">Blogs</span></h2>
  <div class="blog-grid">
    <article class="post">
      <div class="post-photo" role="img" aria-label="Soldier aiming a rifle in dusty terrain" style="background:linear-gradient(135deg,#5c5346,#3a352d)"><div class="post-date">12<br>JUN</div></div>
      <h4>Lorem amet, consectetur adipiscing</h4>
      <p>Lorem ipsum dolor sit amet, consectetur adipiscing elit, sed do eiusmod tempor incididunt ut labore et dolore magna aliqua.</p>
      <a href="#">LEARN MORE ›</a>
    </article>
    <article class="post">
      <div class="post-photo" role="img" aria-label="Soldiers moving through an orange smoky battlefield" style="background:linear-gradient(135deg,#c98a4a,#8a5a32)"><div class="post-date">12<br>JUN</div></div>
      <h4>Lorem amet, consectetur adipiscing</h4>
      <p>Lorem ipsum dolor sit amet, consectetur adipiscing elit, sed do eiusmod tempor incididunt ut labore et dolore magna aliqua.</p>
      <a href="#">LEARN MORE ›</a>
    </article>
    <article class="post">
      <div class="post-photo" role="img" aria-label="Armed soldier crouching among green foliage" style="background:linear-gradient(135deg,#4d5a36,#2c3322)"><div class="post-date">12<br>JUN</div></div>
      <h4>Lorem amet, consectetur adipiscing</h4>
      <p>Lorem ipsum dolor sit amet, consectetur adipiscing elit, sed do eiusmod tempor incididunt ut labore et dolore magna aliqua.</p>
      <a href="#">LEARN MORE ›</a>
    </article>
  </div>
</section>

<section class="cta">
  <div class="news">
    <h2 class="heading">Sign Up to Our Newsletter</h2>
    <p>Get the inside scoop on product releases, exclusive offers, and more...</p>
    <div class="subscribe"><span>Enter Your Email</span><b>SUBSCRIBE</b></div>
  </div>
  <div class="about">
    <h2 class="heading">Want to Know More About Us?</h2>
    <p>Lorem ipsum dolor sit amet, consectetur adipiscing elit, sed do eiusmod tempor incididunt ut</p>
    <a class="btn btn-white" href="#">Learn More</a>
  </div>
</section>

<footer class="footer">
  <div>
    <div class="brand"><i></i>U.S. TORVANE</div>
    <div class="social"><i></i><i></i><i></i><i></i></div>
  </div>
  <div class="links">
    <ul style="list-style:none"><li>Our Products</li><li>Our Story</li><li>Shop by use</li><li>About</li><li>Contact Us</li></ul>
    <ul style="list-style:none"><li>Contact Us</li><li>Terms &amp; Conditions</li><li>Returns &amp; Refunds</li><li>Take the Quiz</li><li>FAQ</li></ul>
  </div>
  <div class="help">
    <div>Need Help?</div>
    <div class="phone"><svg width="18" height="18" viewBox="0 0 24 24" fill="#fff"><path d="M6.6 10.8a15 15 0 006.6 6.6l2.2-2.2c.3-.3.7-.4 1-.2 1.1.4 2.3.6 3.6.6.6 0 1 .4 1 1V20c0 .6-.4 1-1 1A17 17 0 013 4c0-.6.4-1 1-1h3.5c.6 0 1 .4 1 1 0 1.3.2 2.5.6 3.6.1.3 0 .7-.2 1z"/></svg>800 555 0142</div>
    <div>We're always looking to improve</div>
    <a class="btn btn-red" href="#">Leave Feedback</a>
  </div>
</footer>
<div class="copyright">Copyright © 2020 . USTORVANE. All Rights Reserved.</div>

</body>
</html>
```